Kellwyn Surface Records

I have a current web site that it looking quite aged and it needs a new lease of life. This is a Graffiti Management Website so is all about data processing and management of information. I want a html 5 view on any platform design. clean crisp and new. I have provided some screen shots of my current site.

Target Market(s)

The Target Market will be local government. most users will not be heavy pc users

Industry/Entity Type

Management

Font styles to use
Sans Serif
Other font styles liked:
• web font like calibri

Colors

Designer to choose colors to be used in the design.

Requirements
Must have
• Must have menus similar to attachments

```html
<!DOCTYPE html>
<html lang="en">
<head>
<meta charset="utf-8">
<title>Kellwyn Surface Records</title>
<link href="https://fonts.googleapis.com/css2?family=Open+Sans:wght@400;600;700&display=swap" rel="stylesheet">
<style>
:root{
  --blue:#1d87c8;
  --blue-dark:#136aa3;
  --ink:#333a42;
  --muted:#6b737b;
  --light:#eef1f4;
  --panel:#ffffff;
  --dark:#262d35;
  --footer:#2f3843;
  --orange:#e5782a;
  --rule:#d4dae0;
}
*{box-sizing:border-box;margin:0;padding:0}
html,body{width:863px;height:1200px;overflow:hidden}
body{font-family:"Open Sans",Arial,sans-serif;color:var(--ink);background:var(--panel);position:relative}

/* header */
.site-header{height:62px;position:relative;background:var(--panel)}
.brand{position:absolute;left:34px;top:8px}
.brand-name{font-size:26px;font-weight:600;color:var(--blue);letter-spacing:1px;line-height:30px}
.brand-sub{font-size:8px;font-weight:600;color:var(--ink);letter-spacing:.5px;text-transform:uppercase}
.account-links{position:absolute;right:34px;top:8px;display:flex;gap:4px}
.account-links a{font-size:8px;font-weight:600;color:#fff;text-decoration:none;padding:3px 9px;background:var(--muted)}
.account-links a.login{background:var(--blue)}
.main-nav{position:absolute;right:34px;top:36px;display:flex}
.main-nav a{font-size:9px;font-weight:600;color:var(--ink);text-decoration:none;padding:6px 11px;text-transform:uppercase}
.main-nav a.active{background:var(--blue);color:#fff}

/* hero */
.hero{position:relative;height:332px;background:linear-gradient(135deg,#cfe3f3 0%,#8fb9dc 35%,#3e78ad 70%,#1d4c7c 100%)}
.hero-caption{position:absolute;left:310px;top:190px;font-size:15px;font-weight:600;color:#fff;letter-spacing:1px}
.hero-arrow{position:absolute;top:150px;width:24px;height:34px;background:rgba(0,0,0,.45);display:flex;align-items:center;justify-content:center}
.hero-arrow.prev{left:97px}
.hero-arrow.next{right:97px}

/* products */
.products{background:var(--light);height:401px;position:relative;padding-top:36px}
.section-tag{display:block;width:max-content;margin:0 auto;font-size:10px;font-weight:700;color:var(--blue);text-transform:uppercase;border:1px solid var(--blue);padding:6px 16px;background:var(--panel)}
.product-grid{display:grid;grid-template-columns:repeat(4,1fr);gap:20px;padding:0 110px;margin-top:56px}
.product h3{font-size:9px;font-weight:700;color:var(--blue);text-transform:uppercase;margin-bottom:6px}
.product .thumb{height:104px;margin-bottom:8px}
.product p{font-size:8px;line-height:12px;color:var(--ink)}
.product a{display:inline-block;margin-top:6px;font-size:8px;font-weight:700;color:var(--ink);text-decoration:none;text-transform:uppercase}

/* welcome */
.welcome{position:relative;height:243px;background:linear-gradient(180deg,#1f252c 0%,#2c353f 55%,#1d2329 100%);color:#fff;text-align:center;padding-top:30px}
.welcome .section-tag{background:transparent;color:#fff;border-color:#fff}
.welcome p{width:600px;margin:20px auto 0;font-size:9px;line-height:13px;color:#dfe4e9}
.btn-read{display:inline-block;margin-top:22px;background:var(--orange);color:#fff;font-size:8px;font-weight:700;text-decoration:none;padding:8px 16px;text-transform:uppercase}

/* benefits */
.benefits{height:115px;background:var(--light);text-align:center;padding-top:12px}
.benefits .section-tag{font-size:9px;padding:4px 14px}
.benefits-intro{width:560px;margin:8px auto 0;font-size:9px;line-height:12px;color:var(--ink)}
.benefit-row{display:flex;justify-content:center;gap:60px;margin-top:10px}
.benefit{display:flex;align-items:center;gap:6px;text-align:left}
.benefit span{font-size:8px;font-weight:700;line-height:10px;text-transform:uppercase;color:var(--ink)}

/* footer */
.site-footer{position:absolute;left:0;bottom:0;width:863px;height:47px;background:var(--footer);color:#c9d0d7}
.follow{position:absolute;left:34px;top:9px;font-size:8px;font-weight:600;text-transform:uppercase}
.social{display:flex;gap:4px;margin-top:5px}
.social i{display:block;width:13px;height:13px;border-radius:50%;background:var(--blue)}
.footer-nav{position:absolute;right:34px;top:12px;display:flex;gap:10px;font-size:8px;font-weight:600;text-transform:uppercase}
.footer-nav a{color:#fff;text-decoration:none}
.copyright{position:absolute;right:34px;top:27px;font-size:7px}
</style>
</head>
<body>

<header class="site-header">
  <div class="brand">
    <div class="brand-name">KSR</div>
    <div class="brand-sub">Kellwyn Surface Records</div>
  </div>
  <div class="account-links">
    <a href="#">Register</a>
    <a href="#" class="login">Login</a>
  </div>
  <nav class="main-nav">
    <a href="#" class="active">Home</a>
    <a href="#">Products</a>
    <a href="#">Reports</a>
    <a href="#">Benefits</a>
    <a href="#">Legislation</a>
    <a href="#">Contact Us</a>
  </nav>
</header>

<section class="hero" role="img" aria-label="Hand on a computer mouse with glowing data charts and binary digits">
  <div class="hero-caption">ONLINE DATABASE SYSTEM</div>
  <div class="hero-arrow prev"><svg width="10" height="14" viewBox="0 0 10 14"><path d="M8 1 2 7l6 6" fill="none" stroke="#fff" stroke-width="2"/></svg></div>
  <div class="hero-arrow next"><svg width="10" height="14" viewBox="0 0 10 14"><path d="M2 1l6 6-6 6" fill="none" stroke="#fff" stroke-width="2"/></svg></div>
</section>

<section class="products">
  <span class="section-tag">Our Products</span>
  <div class="product-grid">
    <article class="product">
      <h3>Graffiti Poster</h3>
      <div class="thumb" role="img" aria-label="Person photographing graffiti on a wall" style="background:linear-gradient(135deg,#7c8a96,#3f4b57)"></div>
      <p>KSR allows its subscribers to add digital photographs to the register for each site.</p>
      <a href="#">Learn More</a>
    </article>
    <article class="product">
      <h3>Searchable Database</h3>
      <div class="thumb" role="img" aria-label="Tablet showing database search results" style="background:linear-gradient(135deg,#b7c3cc,#5b6b79)"></div>
      <p>KSR allows you to search your own records and those of nearby councils quickly.</p>
      <a href="#">Learn More</a>
    </article>
    <article class="product">
      <h3>Statistical Analysis Reports</h3>
      <div class="thumb" role="img" aria-label="Printed charts and reports on a desk" style="background:linear-gradient(135deg,#d8dde2,#8f9aa4)"></div>
      <p>KSR will allow you to run statistical analysis reports on your removal data.</p>
      <a href="#">Learn More</a>
    </article>
    <article class="product">
      <h3>Data Conversion</h3>
      <div class="thumb" role="img" aria-label="Laptop converting data files" style="background:linear-gradient(135deg,#4d86b8,#1e3f63)"></div>
      <p>KSR can provide a Data Conversion service so that old records carry across.</p>
      <a href="#">Learn More</a>
    </article>
  </div>
</section>

<section class="welcome">
  <span class="section-tag">Welcome to Our Site</span>
  <p>KSR is an Online Database System to Manage Graffiti in your area or your Properties. KSR allows you to Register, Track, Report and Archive Graffiti sites with Photographic Records. KSR reveals both Estimated and Actual hours and costs for each site, enabling you to track the effectiveness of your Graffiti policy. KSR allows sharing of data between subscribers, assisting with tracking of offenders, Statistical and Comparison Reporting Systems to allow its subscribers to graphically report and compare their Graffiti Data.</p>
  <a href="#" class="btn-read">Read More</a>
</section>

<section class="benefits">
  <span class="section-tag">Benefits</span>
  <p class="benefits-intro">KSR allows you to track the cost and effectiveness of your Graffiti Removal. Compare the estimates and actual costs for External Contractors against inhouse removal.</p>
  <div class="benefit-row">
    <div class="benefit">
      <svg width="22" height="22" viewBox="0 0 22 22"><circle cx="11" cy="11" r="10" fill="none" stroke="#333a42" stroke-width="1.5"/><text x="11" y="15" font-size="11" font-weight="700" text-anchor="middle" fill="#333a42" font-family="Open Sans, sans-serif">$</text></svg>
      <span>Cost<br>Effective</span>
    </div>
    <div class="benefit">
      <svg width="22" height="22" viewBox="0 0 22 22"><circle cx="11" cy="11" r="10" fill="none" stroke="#333a42" stroke-width="1.5"/><rect x="5" y="8" width="12" height="8" rx="1" fill="#333a42"/><rect x="8" y="6" width="4" height="2" fill="#333a42"/><circle cx="11" cy="12" r="2.2" fill="#eef1f4"/></svg>
      <span>Photographic<br>Records</span>
    </div>
    <div class="benefit">
      <svg width="22" height="22" viewBox="0 0 22 22"><circle cx="11" cy="11" r="10" fill="none" stroke="#333a42" stroke-width="1.5"/><circle cx="11" cy="8.5" r="2.6" fill="#333a42"/><path d="M6 16c0-3 2.2-4.5 5-4.5s5 1.5 5 4.5z" fill="#333a42"/></svg>
      <span>Assist<br>Prosecution</span>
    </div>
    <div class="benefit">
      <svg width="22" height="22" viewBox="0 0 22 22"><circle cx="11" cy="11" r="10" fill="none" stroke="#333a42" stroke-width="1.5"/><rect x="7" y="10" width="8" height="6" fill="#333a42"/><path d="M8.5 10V8a2.5 2.5 0 0 1 5 0v2" fill="none" stroke="#333a42" stroke-width="1.5"/></svg>
      <span>Access<br>and Security</span>
    </div>
  </div>
</section>

<footer class="site-footer">
  <div class="follow">Follow Us On
    <div class="social"><i></i><i></i><i></i></div>
  </div>
  <nav class="footer-nav">
    <a href="#">Home</a><a href="#">Products</a><a href="#">Reports</a><a href="#">Benefits</a><a href="#">Legislation</a><a href="#">Contact Us</a>
  </nav>
  <div class="copyright">Copyright © 2015 KSR. All Rights Reserved</div>
</footer>

</body>
</html>
```